Stonebrace Business Card Design

The Stonebrace Co is an aggregate (crushing) equipment dealer serving Western Canadian provinces. Stonebrace is a distributor of aggregate equipment for different manufacturers.

We are looking to change and update the existing business card which has been used since the existence of the company. A copy of existing card has been attached for reference. The Stonebrace Co logo we want to remain the same and we want the green color to remain the same.

We are wanting something new with a different look. A refreshing card to show a new modern and updated look. No longer wanting to have the manufacturers on the back of the card but something more like our logo on the back of the card with a statement like "Crushing Solutions"

ideas could be:
- card can be different colors on front and back
- front or reverse of the card could possibly be the green color with the logo in black

Target Market(s)

Owners of Aggregate/Crushing companies

Contact Information for Business Card

see above

Requirements
Must have
• - logo to remain same along with same font within logo
• - green color to remain same
Nice to have
• as noted above under project description
Should not have

```html
<!DOCTYPE html>
<html lang="en">
<head>
<meta charset="utf-8">
<title>The Stonebrace Co – Business Card</title>
<link href="https://fonts.googleapis.com/css2?family=Roboto:wght@400;500;700&display=swap" rel="stylesheet">
<style>
  :root {
    --brand-green: #8a8b0b;
    --ink: #231f20;
    --paper: #f4f4f3;
    --backdrop: #e6e4e0;
    --white: #ffffff;
  }
  * { margin: 0; padding: 0; box-sizing: border-box; }
  html, body { width: 1200px; height: 960px; overflow: hidden; }
  body {
    background: var(--backdrop);
    font-family: "Roboto", Arial, sans-serif;
    position: relative;
  }
  .card {
    position: absolute;
    left: 320px;
    width: 600px;
    height: 345px;
    border-radius: 18px;
    overflow: hidden;
    box-shadow: 0 3px 8px rgba(0,0,0,0.25);
  }
  /* Front */
  .card-front { top: 100px; background: var(--brand-green); }
  .card-front .wordmark {
    position: absolute; top: 165px; left: 0; right: 0;
    display: flex; justify-content: center; align-items: center; gap: 16px;
  }
  .wordmark-dot { width: 34px; height: 34px; border-radius: 50%; background: var(--ink); }
  .wordmark-name {
    font-weight: 700; font-size: 21px; letter-spacing: 0.2px; color: var(--ink);
  }
  .tagline {
    position: absolute; top: 298px; left: 0; right: 0; text-align: center;
    font-weight: 500; font-size: 15px; color: var(--ink);
  }
  /* Back */
  .card-back { top: 493px; background: var(--paper); }
  .card-back .wordmark {
    position: absolute; top: 110px; left: 0; right: 0;
    display: flex; justify-content: center; align-items: center; gap: 16px;
  }
  .card-back .wordmark-dot { background: var(--brand-green); width: 40px; height: 40px; }
  .card-back .wordmark-name { font-size: 21px; }
  .contact-band {
    position: absolute; top: 200px; left: 0; right: 0; height: 107px;
    background: var(--brand-green); color: var(--white);
  }
  .person { position: absolute; left: 27px; top: 12px; }
  .person-name { font-weight: 700; font-size: 20px; line-height: 24px; }
  .person-title { font-weight: 500; font-size: 15px; line-height: 20px; margin-top: 2px; }
  .person-address { font-size: 14px; line-height: 18px; margin-top: 6px; }
  .channels { position: absolute; right: 26px; top: 20px; list-style: none; }
  .channels li {
    display: flex; justify-content: flex-end; align-items: center; gap: 10px;
    font-size: 14px; line-height: 20px;
  }
  .channels svg { width: 14px; height: 14px; fill: var(--white); }
  .site-band {
    position: absolute; top: 311px; left: 0; right: 0; bottom: 0;
    background: var(--ink); color: var(--white);
    text-align: center; font-size: 14px; letter-spacing: 7px; line-height: 34px;
  }
</style>
</head>
<body>
  <section class="card card-front">
    <div class="wordmark">
      <span class="wordmark-dot"></span>
      <span class="wordmark-name">THE STONEBRACE CO.</span>
    </div>
    <p class="tagline">Crushing Solutions</p>
  </section>

  <section class="card card-back">
    <div class="wordmark">
      <span class="wordmark-dot"></span>
      <span class="wordmark-name">THE STONEBRACE CO.</span>
    </div>
    <div class="contact-band">
      <div class="person">
        <p class="person-name">DALE MORROW</p>
        <p class="person-title">CEO/FOUNDER</p>
        <p class="person-address">2218- 48B Avenue<br>Camrose, Alberta T4V 1K2</p>
      </div>
      <ul class="channels">
        <li>780.555.0142
          <svg viewBox="0 0 16 16" aria-hidden="true"><path d="M3.6 1.2l2.3 2.9-1.4 1.6c.9 2 2.6 3.7 4.6 4.6l1.6-1.4 2.9 2.3-1.3 2.4C7 13.6 2.4 9 .9 2.5z"/></svg>
        </li>
        <li>780.555.0187
          <svg viewBox="0 0 16 16" aria-hidden="true"><path d="M4 0h8a1 1 0 0 1 1 1v14a1 1 0 0 1-1 1H4a1 1 0 0 1-1-1V1a1 1 0 0 1 1-1zm.6 1.8v10.6h6.8V1.8zM8 13.3a.9.9 0 1 0 0 1.8.9.9 0 0 0 0-1.8z"/></svg>
        </li>
        <li>780.555.0163
          <svg viewBox="0 0 16 16" aria-hidden="true"><path d="M4 1h8v4H4zM1 6h14v6h-2v3H3v-3H1zm3.5 4.5v3h7v-3z"/></svg>
        </li>
        <li>dale@stonebr.com
          <svg viewBox="0 0 16 16" aria-hidden="true"><path d="M1 3h14v1.2L8 9 1 4.2zm0 2.8l7 4.8 7-4.8V13H1z"/></svg>
        </li>
      </ul>
    </div>
    <div class="site-band">www.stonebrace.ca</div>
  </section>
</body>
</html>
```